Company or website name
- The Steadfast Haulers and Storage
- Links to the website
- Pinecrestcartage.com
- Describe your company and organization and target audience
- Residential and commercial moving and relocation service that needs a website redesign.
- The design should have the following
- I NEED THE WEBSITE TO BE SIMPLE AND STRAIGHT TO THE POINT...MAIN CONCERN IS THAT THEY FILL OUT INFORMATION TO GET QUOTE. SITE EXAMPLE THAT I LIKE IS ( WWW.MYDORVALS.COM) https://www.corvellfreight.com/

```html
<!DOCTYPE html>
<html lang="en">
<head>
<meta charset="utf-8">
<title>The Steadfast Haulers and Storage</title>
<link href="https://fonts.googleapis.com/css2?family=Roboto:wght@400;500;700;900&display=swap" rel="stylesheet">
<style>
:root{
  --blue:#3a5ca8;
  --blue-dark:#2e4b8f;
  --yellow:#f7c51b;
  --ink:#1d2433;
  --light:#f1f1f1;
  --field:#dcdcdc;
  --white:#ffffff;
}
*{box-sizing:border-box;margin:0;padding:0}
html,body{width:1200px;height:3452px;overflow:hidden}
body{position:relative;font-family:'Roboto',Arial,sans-serif;color:var(--ink);background:var(--white)}
.abs{position:absolute}

/* hero */
.hero{left:0;top:0;width:1200px;height:674px;overflow:hidden}
.hero-photo{position:absolute;inset:0;background:linear-gradient(180deg,#4e5e86 0%,#6b7fa8 30%,#7d8aa4 55%,#535c6e 75%,#3e4656 100%)}
.hero-tint{position:absolute;inset:0;background:rgba(46,75,143,.35)}
.topbar{position:absolute;right:62px;top:2px;color:var(--white);font-size:17px;display:flex;align-items:center;gap:6px}
.brand{position:absolute;left:65px;top:50px;display:flex;align-items:center;gap:12px;color:var(--white);font-weight:700;font-size:40px;letter-spacing:2px}
.brand-dot{width:36px;height:36px;border-radius:50%;background:var(--white)}
.nav{position:absolute;top:66px;left:458px;font-size:17px;color:var(--white)}
.nav a{color:var(--white);text-decoration:none;position:absolute;white-space:nowrap}
.btn{display:inline-flex;align-items:center;justify-content:center;background:var(--yellow);color:var(--ink);font-weight:500;border-radius:4px;text-decoration:none}
.nav-cta{position:absolute;left:1006px;top:62px;width:132px;height:35px;font-size:16px}
.hero-copy{position:absolute;left:0;width:1200px;top:245px;text-align:center;color:var(--white)}
.hero-copy h1{font-size:64px;font-weight:900;line-height:1.05}
.hero-copy h2{font-size:39px;font-weight:700;margin-top:6px}
.hero-copy p{font-size:20px;font-weight:500;margin-top:8px}
.hero-cta{position:absolute;left:458px;top:418px;width:278px;height:48px;font-size:26px}

/* about */
.about{left:0;top:674px;width:1200px;height:459px;background:var(--light)}
.sec-title{font-size:37px;font-weight:700;color:var(--blue);line-height:1.2}
.sec-title .accent{color:var(--yellow);display:block}
.about .sec-title{position:absolute;left:62px;top:80px}
.body-text{font-size:14px;line-height:20px;color:var(--blue-dark);font-weight:500}
.about-text{position:absolute;left:62px;top:190px;width:560px}
.about-text p+p{margin-top:20px}
.gallery{position:absolute;left:677px;top:35px;width:461px;height:394px;border:4px solid var(--yellow);display:grid;grid-template-columns:1fr 1fr;grid-template-rows:1fr 1fr;gap:4px;background:var(--yellow)}
.gallery div{width:100%;height:100%}

/* services */
.services{left:0;top:1133px;width:1200px;height:587px;background:var(--white)}
.services .sec-title{position:absolute;left:62px;top:92px}
.services .intro{position:absolute;left:62px;top:148px;width:560px;font-size:14px;line-height:20px;font-weight:500;color:var(--ink)}
.service{position:absolute;top:236px;width:260px;text-align:center}
.service-ring{width:206px;height:206px;border-radius:50%;border:5px solid var(--yellow);margin:0 auto;display:flex;align-items:center;justify-content:center;background:var(--white)}
.service-ring.filled{background:var(--blue)}
.service span{display:block;margin-top:30px;font-size:20px;color:var(--blue);font-weight:500}

/* testimonials */
.reviews{left:0;top:1720px;width:1200px;height:459px;background:var(--light)}
.reviews .sec-title{position:absolute;left:62px;top:52px;font-size:35px}
.avatar{position:absolute;left:140px;top:160px;width:216px;height:216px;border-radius:50%;background:radial-gradient(circle at 50% 40%,#e0a46b,#c98a4e 55%,#e9e4da 100%)}
.review-name{position:absolute;left:386px;top:180px;font-size:27px;color:var(--blue);font-weight:500}
.review-place{position:absolute;left:386px;top:214px;font-size:19px;color:var(--yellow)}
.review-text{position:absolute;left:386px;top:258px;width:700px;font-size:21px;line-height:32px;color:#444}
.dots{position:absolute;top:406px;left:532px;display:flex;gap:22px}
.dots i{display:block;width:9px;height:9px;border-radius:50%;background:#a8b4d4}
.dots i.on{background:var(--blue)}

/* quote form */
.quote{left:0;top:2179px;width:1200px;height:968px;background:linear-gradient(135deg,#8a96ac 0%,#6d7a92 40%,#9aa3b4 70%,#6b7890 100%)}
.quote-card{position:absolute;left:154px;top:81px;width:890px;height:809px;background:#f6f6f6;border-radius:4px;box-shadow:0 6px 18px rgba(0,0,0,.3)}
.form-label{position:absolute;left:89px;font-size:20px;font-weight:500;color:var(--blue)}
.field{position:absolute;height:32px;background:var(--field);font-size:18px;color:#9a9a9a;padding:5px 10px;display:flex;align-items:center;justify-content:space-between}
.field.l{left:73px;width:361px}
.field.r{left:453px;width:364px}
.field .caret{width:0;height:0;border-left:5px solid transparent;border-right:5px solid transparent;border-top:6px solid #555}
.form-cta{position:absolute;left:323px;top:714px;width:246px;height:48px;font-size:26px;border-radius:5px}

/* footer */
.footer{left:0;top:3147px;width:1200px;height:305px;background:var(--blue);color:var(--white)}
.footer-brand{position:absolute;left:62px;top:44px;display:flex;align-items:center;gap:10px;font-size:34px;font-weight:700;letter-spacing:2px}
.footer-brand .brand-dot{width:28px;height:28px}
.badge{position:absolute;left:105px;top:148px;width:72px;height:28px;background:#1d2d55}
.foot-col{position:absolute;top:44px}
.foot-col h4{font-size:20px;color:var(--yellow);font-weight:700;margin-bottom:10px}
.foot-col li{list-style:none;font-size:15px;line-height:22px;white-space:nowrap}
.legal{position:absolute;left:0;width:1200px;text-align:center;font-size:14px;color:#c7d0e6}
</style>
</head>
<body>

<header class="hero abs">
  <div class="hero-photo" role="img" aria-label="Photo of a moving truck on a mountain highway"></div>
  <div class="hero-tint"></div>
  <div class="topbar">
    <svg width="14" height="14" viewBox="0 0 24 24"><path fill="#fff" d="M6.6 10.8a15 15 0 0 0 6.6 6.6l2.2-2.2c.3-.3.7-.4 1-.2 1.1.4 2.3.6 3.6.6.6 0 1 .4 1 1V20c0 .6-.4 1-1 1A17 17 0 0 1 3 4c0-.6.4-1 1-1h3.5c.6 0 1 .4 1 1 0 1.3.2 2.5.6 3.6.1.3 0 .7-.2 1z"/></svg>
    (203) 555-0142
  </div>
  <div class="brand"><span class="brand-dot"></span>STEADFAST</div>
  <nav class="nav">
    <a style="left:0">Home</a>
    <a style="left:81px">Services ⌄</a>
    <a style="left:200px">About</a>
    <a style="left:305px">Careers</a>
    <a style="left:421px">Moving Labor</a>
  </nav>
  <a class="btn nav-cta">GET A QUOTE</a>
  <div class="hero-copy">
    <h1>WHERE ARE YOU MOVING?</h1>
    <h2>WE HELP MOVE LIVES FORWARD</h2>
    <p>Providing Local, Long Distance Residential and Commercial Moving Services Since 2006</p>
  </div>
  <a class="btn hero-cta">GET A FREE QUOTE</a>
</header>

<section class="about abs">
  <h2 class="sec-title">Moving Families &amp; Businesses<span class="accent">For Over A Decade</span></h2>
  <div class="about-text body-text">
    <p>As movers since 2007, Steadfast Inc has an expertise in transportation and storage services that is unequaled by other moving companies.</p>
    <p>At Steadfast Inc we coordinate local, long distance moves that incorporate all the necessary moving services to set serve your individual move. In addition, we offer our commercial clients a wide array of specialized transportation services for high value products. We are committed to safe, simple moving experiences for family, businesses and employees.</p>
  </div>
  <div class="gallery">
    <div role="img" aria-label="Photo of a moving truck" style="background:linear-gradient(135deg,#6f8e5a,#c9ccd2)"></div>
    <div role="img" aria-label="Photo of a mover carrying boxes" style="background:linear-gradient(135deg,#c9a21a,#7a6a2a)"></div>
    <div role="img" aria-label="Photo of a storage unit corridor" style="background:linear-gradient(135deg,#e6a11e,#b06a12)"></div>
    <div role="img" aria-label="Photo of a senior couple at home" style="background:linear-gradient(135deg,#c5b6a2,#8d7f73)"></div>
  </div>
</section>

<section class="services abs">
  <h2 class="sec-title">Moving Services</h2>
  <p class="intro">As movers since 2007, Steadfast Inc has an expertise in transportation and storage services that is unequaled by other moving companies.</p>
  <div class="service" style="left:35px">
    <div class="service-ring filled">
      <svg width="110" height="100" viewBox="0 0 110 100"><path fill="#f7c51b" d="M55 6 4 48h14v46h74V48h14z"/><rect x="42" y="58" width="26" height="36" fill="#3a5ca8"/></svg>
    </div>
    <span>Residential Moving</span>
  </div>
  <div class="service" style="left:323px">
    <div class="service-ring" role="img" aria-label="Commercial moving icon"></div>
    <span>Commercial Moving</span>
  </div>
  <div class="service" style="left:614px">
    <div class="service-ring">
      <svg width="120" height="90" viewBox="0 0 120 90"><rect x="4" y="8" width="70" height="58" rx="4" fill="#3a5ca8"/><path fill="#3a5ca8" d="M78 26h22l16 20v20H78z"/><circle cx="26" cy="72" r="11" fill="#3a5ca8" stroke="#fff" stroke-width="4"/><circle cx="94" cy="72" r="11" fill="#3a5ca8" stroke="#fff" stroke-width="4"/></svg>
    </div>
    <span>Senior Moving</span>
  </div>
  <div class="service" style="left:906px">
    <div class="service-ring">
      <svg width="100" height="100" viewBox="0 0 100 100"><path fill="#3a5ca8" d="M50 6 6 30v64h88V30z"/><rect x="26" y="44" width="48" height="50" fill="#fff"/><rect x="30" y="48" width="40" height="46" fill="#3a5ca8"/></svg>
    </div>
    <span>Storage</span>
  </div>
</section>

<section class="reviews abs">
  <h2 class="sec-title">What Customers Are Saying</h2>
  <div class="avatar" role="img" aria-label="Customer portrait photo"></div>
  <div class="review-name">Name Surname</div>
  <div class="review-place">San Antonio TX</div>
  <p class="review-text">Great Service, Easy, Stress free move. Provided accurate move estimate. Professional staff all around. From Estimate to delivery. Professional and Friendly pickup, Transportation, and Delivery. Thank You so Much.</p>
  <div class="dots"><i></i><i></i><i class="on"></i><i></i><i></i></div>
</section>

<section class="quote abs" role="img" aria-label="Aerial photo of a truck yard">
  <form class="quote-card">
    <div class="form-label" style="top:50px">Choose Services</div>
    <div class="field l" style="top:103px">Residential move<i class="caret"></i></div>
    <div class="field r" style="top:103px">Move date</div>
    <div class="field l" style="top:148px">Select move size<i class="caret"></i></div>

    <div class="form-label" style="top:206px">Pickup Location</div>
    <div class="field l" style="top:262px">Zip</div>
    <div class="field r" style="top:262px">City</div>
    <div class="field l" style="top:310px">Select state<i class="caret"></i></div>

    <div class="form-label" style="top:364px">Destination</div>
    <div class="field l" style="top:421px">Zip</div>
    <div class="field r" style="top:421px">City</div>
    <div class="field l" style="top:469px">Select state<i class="caret"></i></div>

    <div class="form-label" style="top:534px">Detail</div>
    <div class="field l" style="top:588px">Name</div>
    <div class="field r" style="top:588px">Email</div>
    <div class="field l" style="top:637px">Phone</div>

    <a class="btn form-cta">Free Quote Now</a>
  </form>
</section>

<footer class="footer abs">
  <div class="footer-brand"><span class="brand-dot"></span>STEADFAST</div>
  <div class="badge"></div>
  <div class="foot-col" style="left:334px">
    <h4>Services</h4>
    <ul><li>Home</li><li>About Us</li><li>Privacy Policy</li><li>Terms and Conditions</li></ul>
  </div>
  <div class="foot-col" style="left:572px">
    <h4>Quick Links</h4>
    <ul><li>Home</li><li>About Us</li><li>Privacy Policy</li><li>Terms and Conditions</li></ul>
  </div>
  <div class="foot-col" style="left:809px">
    <h4>Headquarters</h4>
    <ul><li>The Steadfast Haulers and Storage</li><li>418 Harbor Lane</li><li>Alderbrook, CT 06491</li><li>Connecticut 203-555-0142</li><li>Michigan 248-555-0177</li></ul>
  </div>
  <p class="legal" style="top:248px">Privacy Policy | Site Map | Terms of Use</p>
  <p class="legal" style="top:270px">© 2012 - 2020. All Rights Reserved. The Steadfast Haulers and Storage</p>
</footer>

</body>
</html>
```